Velmor Spire Nine Flash website

we need a website to cater to 2 aspect of the business. We have Velmor spire residence and velmor spire office. For the office, we will get their inquire and arrange a face to face meetup to show them the office area for rent. For the residence side, it will need to be like staylane or roomvio.com. we want to allow them to book online for the date they need. We have a total of 10 different room configurations starting at $70 per night and up depending on the size of the room. example of the design is https://brisquelodge.com/

Target Market(s)

the website should have detail information on the layout, designs, and luxury of the building.

Industry/Entity Type

office and service appartment rental/lease

Coding

Coded - Design and coding required

Number of Pages Required

5+ page

Requirements
Must have
• a luxury perspective
Nice to have
• example https://brisquelodge.com/

```html
<!DOCTYPE html>
<html lang="en">
<head>
<meta charset="utf-8">
<title>Velmor Spire Nine</title>
<link href="https://fonts.googleapis.com/css2?family=Merriweather:wght@700;900&family=Poppins:wght@400;500;600&display=swap" rel="stylesheet">
<style>
:root{
  --gold:#E2BC75;
  --gold-deep:#D9AE5E;
  --band:#EEDAB2;
  --form:#E2BF78;
  --field:#EAD29D;
  --footer:#E5C27C;
  --ink:#2A2A2A;
  --muted:#6E6E6E;
  --white:#FFFFFF;
}
*{box-sizing:border-box;margin:0;padding:0}
html,body{width:1200px;height:4297px;overflow:hidden}
body{position:relative;background:var(--white);font-family:'Poppins',sans-serif;color:var(--ink)}
.abs{position:absolute}
.serif{font-family:'Merriweather',serif;font-weight:700}

/* nav */
.brand{left:88px;top:18px;width:140px;text-align:center;color:var(--gold-deep);font-size:15px;letter-spacing:.5px}
.brand-mark{display:block;width:36px;height:36px;margin:0 auto 6px;border:2px solid var(--gold-deep)}
.nav{left:319px;top:38px;display:flex;gap:25px;font-size:18px;color:#444}
.nav .active{color:var(--gold-deep);text-decoration:underline;text-underline-offset:4px}
.btn{background:var(--gold);color:var(--white);border-radius:30px;display:flex;align-items:center;justify-content:center;font-weight:500}
.nav-cta{left:955px;top:23px;width:160px;height:52px;font-size:19px}

/* hero */
.hero{left:0;top:108px;width:1200px;height:516px;background:linear-gradient(120deg,#3b3b3b,#6a6a6a 45%,#8b8b8b 70%,#4f4f4f)}
.hero-title{left:0;top:258px;width:1200px;text-align:center;color:var(--white);font-size:40px}
.hero-text{left:140px;top:325px;width:920px;text-align:center;color:var(--white);font-size:19.5px;line-height:31px}
.hero-cta{left:509px;top:442px;width:179px;height:52px;font-size:19px}

/* partners */
.partners{left:85px;top:660px;width:1030px;display:flex;justify-content:space-between;align-items:center;font-size:24px;font-weight:600;color:#555}
.partner{display:flex;align-items:center;gap:8px}
.partner i{display:block;width:24px;height:24px;background:#888}

/* discover */
.photo{background:linear-gradient(160deg,#5a5a5a,#9b9b9b 60%,#3f3f3f)}
.h2{font-size:27px}
.discover-title{left:600px;top:836px}
.body-text{font-size:20.5px;line-height:30px;color:var(--muted)}
.discover-text{left:600px;top:884px;width:510px}
.stat{width:185px;height:110px;background:var(--band);border-radius:10px;text-align:center;padding-top:16px}
.stat b{display:block;font-size:32px;font-weight:600}
.stat span{font-size:19px}

/* offerings */
.center{left:0;width:1200px;text-align:center}
.band{background:var(--band)}
.card-title{font-size:23px;font-weight:500}
.card-text{font-size:20.5px;line-height:30px;color:#555}

/* why */
.feature{width:230px;text-align:center}
.feature-icon{width:84px;height:84px;margin:0 auto;background:var(--gold);border-radius:10px;display:flex;align-items:center;justify-content:center}
.feature h3{font-size:20px;font-weight:500;margin-top:25px}
.feature p{font-size:18.5px;line-height:27.5px;color:var(--muted);margin-top:18px}

/* contact */
.contact-box{left:544px;top:3321px;width:573px;height:468px;background:var(--form)}
.contact-title{left:578px;top:3368px;color:var(--white);font-size:29px}
.field{height:50px;background:var(--field);border-radius:6px;color:var(--white);font-size:21px;padding-left:18px;display:flex;align-items:center}
.submit{left:578px;top:3697px;width:162px;height:51px;border:2px solid var(--white);border-radius:30px;color:var(--white);font-size:17px;font-weight:500;display:flex;align-items:center;justify-content:center}

/* footer */
.footer{left:0;top:3961px;width:1200px;height:336px;background:var(--footer)}
.foot-brand{left:83px;top:4014px;width:154px;color:var(--white);font-size:17px;text-align:center}
.foot-brand .brand-mark{border-color:var(--white);width:44px;height:44px}
.social{top:4126px;width:40px;height:40px;border-radius:50%;background:var(--white)}
.foot-col h4{color:var(--white);font-size:21px;font-weight:600;margin-bottom:14px}
.foot-col a{display:block;color:var(--white);text-decoration:none;font-size:18px;line-height:39px}
.rule{left:83px;top:4236px;width:1034px;height:1px;background:var(--white)}
.legal{top:4254px;color:var(--white);font-size:20px;font-weight:500}
</style>
</head>
<body>

<!-- navigation -->
<div class="abs brand"><span class="brand-mark"></span>Velmor Spire Nine</div>
<nav class="abs nav">
  <span class="active">Design</span><span>Location</span><span>Experience</span><span>About Us</span><span>Register Now</span>
</nav>
<div class="abs btn nav-cta">Contact Us</div>

<!-- hero -->
<div class="abs hero" role="img" aria-label="Office interior with a potted palm by tall windows and a laptop on a desk"></div>
<h1 class="abs serif hero-title">Welcome Velmor Spire Nine</h1>
<p class="abs hero-text">We need a website to cater to 2 aspect of the business. We have Velmor spire residence and velmor spire office. For the office, we will get their inquire and arrange a face to face meetup to show them the office area for rent.</p>
<div class="abs btn hero-cta">Learn More</div>

<!-- partners -->
<div class="abs partners">
  <div class="partner">Brindleway<i></i></div>
  <div class="partner">quillora</div>
  <div class="partner"><i></i>HarbourLink+</div>
  <div class="partner">Marrow Legal</div>
  <div class="partner">Fairstep Academy<i></i></div>
</div>

<!-- discover -->
<div class="abs photo" style="left:83px;top:883px;width:122px;height:397px" role="img" aria-label="Glass-walled office corridor"></div>
<div class="abs photo" style="left:214px;top:885px;width:359px;height:116px" role="img" aria-label="Concrete office ceiling with lights"></div>
<div class="abs photo" style="left:214px;top:1013px;width:359px;height:129px" role="img" aria-label="Meeting room with chairs and pendant lamps"></div>
<div class="abs photo" style="left:214px;top:1158px;width:359px;height:122px" role="img" aria-label="Polished office floor"></div>
<h2 class="abs serif h2 discover-title">Discover Your Ideal Space</h2>
<p class="abs body-text discover-text">Whether you're seeking a temporary home away from home or a professional environment to foster productivity Velmor Spire Nine offers a curated selection of premium hotel and office spaces to meet your needs</p>
<div class="abs stat" style="left:600px;top:1060px"><b>14K</b><span>Costumers</span></div>
<div class="abs stat" style="left:804px;top:1060px"><b>144+</b><span>Officers</span></div>
<div class="abs stat" style="left:713px;top:1193px"><b>98%</b><span>Guaranteed</span></div>

<!-- offerings -->
<h2 class="abs serif h2 center" style="top:1385px">Our Offerings</h2>
<p class="abs center body-text" style="top:1434px">Our rentals are relatively cheap and affordable with a modern and minimalist design style</p>

<div class="abs band" style="left:0;top:1507px;width:973px;height:362px;border-radius:0 14px 14px 0"></div>
<h3 class="abs card-title" style="left:83px;top:1540px">Hotel Rentals</h3>
<p class="abs card-text" style="left:83px;top:1590px;width:570px">Indulge in the ultimate comfort and luxury with our meticulously designed hotel suites. From cozy rooms for solo travelers to spacious suites for families, each accommodation is crafted to exceed your expectations. Enjoy world-class hospitality, premium amenities, and personalized service throughout your stay.</p>
<div class="abs" style="left:721px;top:1561px;width:396px;height:385px;background:linear-gradient(180deg,#6b4a2f,#4f6a3c 35%,#3f9ab8 65%,#8a6a4a)" role="img" aria-label="Terrace with wicker chairs overlooking a pool and garden pavilion"></div>

<div class="abs band" style="left:225px;top:2016px;width:975px;height:361px;border-radius:14px 0 0 14px"></div>
<div class="abs" style="left:83px;top:2070px;width:396px;height:385px;background:linear-gradient(160deg,#2e2e2e,#7b7b7b 50%,#bdbdbd)" role="img" aria-label="Open-plan office with people working at a long table"></div>
<h3 class="abs card-title" style="left:504px;top:2049px">Office Rentals</h3>
<p class="abs card-text" style="left:504px;top:2097px;width:580px">Elevate your work environment with our prestigious office spaces. Whether you're a freelancer, entrepreneur, or established corporation, our offices cater to diverse professional needs. Experience modern design, cutting-edge technology, and flexible arrangements that inspire innovation and productivity.</p>

<div class="abs btn" style="left:471px;top:2515px;width:257px;height:52px;font-size:19px">See More Offerings</div>

<!-- why choose -->
<h2 class="abs serif h2 center" style="top:2648px">Why Choose Velmor Spire Nine Rentals?</h2>
<p class="abs center body-text" style="top:2698px">These are the benefits that we provide to all of you for all of your offices and hotels</p>

<div class="abs feature" style="left:90px;top:2792px">
  <div class="feature-icon"><svg width="48" height="48" viewBox="0 0 24 24"><circle cx="12" cy="12" r="10" fill="none" stroke="#fff" stroke-width="1.6"/><path d="M12 6l1.8 3.7 4 .6-2.9 2.8.7 4L12 15.2 8.4 17.1l.7-4L6.2 10.3l4-.6z" fill="#fff"/></svg></div>
  <h3>Exceptional Quality</h3>
  <p>Immerse yourself in opulence and sophistication with our meticulously curated spaces designed for utmost comfort and productivity.</p>
</div>
<div class="abs feature" style="left:352px;top:2792px">
  <div class="feature-icon"><svg width="48" height="48" viewBox="0 0 24 24"><path d="M3 15h4l4 2h5l4-3v2l-5 4H9l-6-2z" fill="#fff"/><path d="M10 9l2.5 2.5L18 5" fill="none" stroke="#fff" stroke-width="2" stroke-linecap="round"/></svg></div>
  <h3>Convenience</h3>
  <p>Streamline your experience with seamless staylane, flexible rental options, and attentive concierge services tailored to your preferences.</p>
</div>
<div class="abs feature" style="left:614px;top:2792px">
  <div class="feature-icon"><svg width="48" height="48" viewBox="0 0 24 24"><path d="M12 2a6 6 0 0 0-6 6c0 5 6 11 6 11s6-6 6-11a6 6 0 0 0-6-6z" fill="#fff"/><circle cx="12" cy="8" r="2.3" fill="#E2BC75"/><rect x="5" y="20" width="14" height="2" fill="#fff"/></svg></div>
  <h3>Prime Locations</h3>
  <p>Explore vibrant cityscapes and business hubs with our strategically located properties, offering convenient access to key attractions and amenities.</p>
</div>
<div class="abs feature" style="left:875px;top:2792px">
  <div class="feature-icon"><svg width="48" height="48" viewBox="0 0 24 24"><circle cx="8" cy="7" r="3" fill="#fff"/><path d="M2 20c0-4 3-6 6-6s6 2 6 6z" fill="#fff"/><rect x="15" y="11" width="6" height="9" rx="1" fill="#fff"/></svg></div>
  <h3>Personalized Service</h3>
  <p>Experience hospitality at its finest with our dedicated team committed to ensuring your satisfaction and well-being throughout your stay.</p>
</div>

<!-- contact -->
<div class="abs" style="left:83px;top:3266px;width:461px;height:570px;background:linear-gradient(150deg,#5c6f7a,#9a8a78 45%,#d07a5c 80%,#3b3b3b)" role="img" aria-label="Two colleagues reviewing work at an office desk"></div>
<div class="abs contact-box"></div>
<h2 class="abs serif contact-title">Contact us</h2>
<div class="abs field" style="left:578px;top:3440px;width:228px">First Name</div>
<div class="abs field" style="left:838px;top:3440px;width:227px">Last Name</div>
<div class="abs field" style="left:578px;top:3518px;width:487px">Email</div>
<div class="abs field" style="left:578px;top:3597px;width:487px">Your Message</div>
<div class="abs submit">Submit Now</div>

<!-- footer -->
<footer class="abs footer"></footer>
<div class="abs foot-brand"><span class="brand-mark"></span>Velmor Spire Nine</div>
<span class="abs social" style="left:83px"></span>
<span class="abs social" style="left:147px"></span>
<span class="abs social" style="left:210px"></span>
<div class="abs foot-col" style="left:409px;top:4023px"><h4>Pathers With Us</h4><a>See Our Partners</a><a>Explore Custom Kits</a><a>Receive Volume Discounts</a></div>
<div class="abs foot-col" style="left:688px;top:4023px"><h4>Support</h4><a>Customer Support</a><a>Technical Assistance</a><a>Press &amp; Media</a></div>
<div class="abs foot-col" style="left:918px;top:4023px"><h4>Contact</h4><a>Exam Request</a><a>Locations</a><a>FAQ</a></div>
<div class="abs rule"></div>
<p class="abs center legal">All Right Reserved / Privacy Policy / Terms and Conditions</p>

</body>
</html>
```